Pebblebrook Plots - Online-only garden installation company

Online-only garden installation company. Our demographic is middle aged / suburban women, and we anticipate Facebook driving traffic to this website, as well as referrals from garden centers. The website must be very simple in design and function.

All orders will be placed through the website, including size of garden (3 options), location in yard, payment, and scheduling of installation date.

The website should employ a 3 step process:

Step 1: Select garden size. Either an 4' X 4', 8' X 4', or 12' X 4'.

Step 2: Select a location. We would like to use google maps to look up a US address, then "drag and drop" one of the garden sizes from step 1 to the location the customer would like us to install the garden at their home.

Step 3: Pick an installation date and pay. Using an online calendar the customer will pick a date, and then pay for the installation via credit card.

The website will be linked to an email account, PebblebrookPlots@mailvale.com to inform us of orders placed.

Target Market(s)

Our demographic is middle aged / suburban women, and we anticipate Facebook driving traffic to this website, as well as referrals from garden centers.

Industry/Entity Type

Coding

Number of Pages Required

Requirements
Must have
• Scheduling and payment options.

```html
<!DOCTYPE html>
<html lang="en">
<head>
<meta charset="utf-8">
<title>Pebblebrook Plots – Garden Installation</title>
<link href="https://fonts.googleapis.com/css2?family=Alfa+Slab+One&family=Roboto+Slab:wght@300;400&family=Lato:wght@400;700&display=swap" rel="stylesheet">
<style>
  :root{
    --white:#ffffff;
    --ink:#3a3a3a;
    --muted:#6b6b6b;
    --rule:#dcdcdc;
    --panel:#3f8a3f;
    --panel-line:rgba(255,255,255,.35);
    --accent:#e2552b;
    --accent-dark:#b9401c;
    --field-btn:#dedede;
    --hero-dark:#1d3414;
    --hero-mid:#3c6a24;
    --hero-light:#6c9a34;
  }
  *{box-sizing:border-box;margin:0;padding:0}
  html,body{width:1200px;height:881px;overflow:hidden}
  body{font-family:"Lato",sans-serif;color:var(--ink);background:var(--white);position:relative}

  .site-header{position:absolute;left:0;top:0;width:1200px;height:75px;background:var(--white);z-index:3}
  .brand{position:absolute;left:74px;top:0;width:152px;height:143px;background:var(--white);display:flex;flex-direction:column;align-items:center;justify-content:center;gap:10px}
  .brand-mark{width:22px;height:22px;background:var(--accent)}
  .brand-name{font-family:"Roboto Slab",serif;font-weight:400;font-size:15px;letter-spacing:.5px;color:var(--ink);text-align:center;line-height:1.2}
  .header-nav{position:absolute;right:0;top:0;height:75px;display:flex}
  .nav-item{height:75px;border-left:1px solid var(--rule);display:flex;align-items:center;justify-content:center}
  .nav-icon{width:80px}
  .nav-login{width:247px;gap:10px;font-size:14px;color:var(--muted);text-transform:uppercase;justify-content:flex-start;padding-left:30px}

  .hero{position:absolute;left:0;top:75px;width:1200px;height:806px;
    background:
      radial-gradient(ellipse 320px 420px at 880px 360px, #b0542a 0%, rgba(176,84,42,0) 70%),
      radial-gradient(ellipse 420px 360px at 330px 300px, var(--hero-light) 0%, rgba(108,154,52,0) 75%),
      linear-gradient(180deg, var(--hero-dark) 0%, var(--hero-mid) 55%, #2a5a1c 80%, var(--hero-dark) 100%);}
  .hero-title{position:absolute;left:0;top:302px;width:1200px;text-align:center;font-family:"Alfa Slab One",serif;font-size:40px;letter-spacing:1px;color:var(--white);text-transform:uppercase;z-index:2}
  .ribbon{position:absolute;left:406px;top:348px;width:386px;height:30px;z-index:2}
  .ribbon-text{position:absolute;left:0;top:348px;width:1200px;height:30px;line-height:30px;text-align:center;font-family:"Roboto Slab",serif;font-size:19px;color:var(--white);z-index:3}

  .order-panel{position:absolute;left:113px;top:592px;width:974px;height:203px;background:var(--panel);opacity:.96;z-index:2}
  .order-panel::before{content:"";position:absolute;inset:10px;border:1px solid var(--panel-line)}
  .order-title{position:absolute;left:0;top:36px;width:100%;text-align:center;font-family:"Roboto Slab",serif;font-weight:300;font-size:32px;color:var(--white)}
  .order-form{position:absolute;left:46px;top:111px;display:flex;gap:10px}
  .field{width:242px;height:46px;background:var(--white);border-radius:2px;display:flex;align-items:center;justify-content:space-between;padding:3px 3px 3px 13px;font-size:14px;color:var(--muted)}
  .field-btn{width:40px;height:40px;background:var(--field-btn);border-radius:2px;display:flex;align-items:center;justify-content:center}
  .search-btn{width:127px;height:46px;background:var(--accent);border-radius:2px;display:flex;align-items:center;justify-content:center;gap:10px;color:var(--white);font-weight:700;font-size:16px;text-transform:uppercase}

  .site-footer{position:absolute;left:0;top:843px;width:1200px;text-align:center;font-size:14px;color:rgba(255,255,255,.8);z-index:2}
</style>
</head>
<body>
  <header class="site-header">
    <div class="brand">
      <span class="brand-mark"></span>
      <span class="brand-name">PEBBLEBROOK<br>PLOTS</span>
    </div>
    <nav class="header-nav">
      <div class="nav-item nav-icon" aria-label="Search">
        <svg width="26" height="26" viewBox="0 0 26 26" fill="none" stroke="#777" stroke-width="1.6"><circle cx="11" cy="11" r="9"/><line x1="17.5" y1="17.5" x2="24" y2="24"/></svg>
      </div>
      <div class="nav-item nav-icon" aria-label="Cart">
        <svg width="26" height="24" viewBox="0 0 26 24" fill="none" stroke="#777" stroke-width="1.5"><path d="M1 3h4l3 12h13l3-9H7"/><line x1="9" y1="9" x2="21" y2="9"/><line x1="9" y1="12" x2="20" y2="12"/><circle cx="10" cy="20" r="1.6"/><circle cx="19" cy="20" r="1.6"/></svg>
      </div>
      <div class="nav-item nav-login">
        <svg width="22" height="26" viewBox="0 0 22 26" fill="none" stroke="#777" stroke-width="1.5"><circle cx="11" cy="8" r="6"/><path d="M1 25c0-6 4.5-10 10-10s10 4 10 10z"/></svg>
        Login / Sign up
      </div>
    </nav>
  </header>

  <main class="hero" role="img" aria-label="Photo of a gardener in an orange shirt and cap kneeling beside green shrubs in a garden"></main>

  <h1 class="hero-title">Pebblebrook Plots</h1>
  <svg class="ribbon" viewBox="0 0 386 30" aria-hidden="true">
    <polygon points="0,4 40,4 40,26 0,26 12,15" fill="var(--accent-dark)"/>
    <polygon points="386,4 346,4 346,26 386,26 374,15" fill="var(--accent-dark)"/>
    <polygon points="30,0 356,0 346,30 40,30" fill="var(--accent)"/>
  </svg>
  <p class="ribbon-text">Only Garden Installation Company</p>

  <section class="order-panel">
    <h2 class="order-title">Order Now Garden Installation Today</h2>
    <form class="order-form">
      <div class="field">Select garden size
        <span class="field-btn"><svg width="10" height="8" viewBox="0 0 10 8"><polygon points="0,0 10,0 5,8" fill="#777"/></svg></span>
      </div>
      <div class="field">Select a location
        <span class="field-btn"><svg width="22" height="22" viewBox="0 0 22 22" fill="none" stroke="#777" stroke-width="1.5"><circle cx="11" cy="11" r="7"/><circle cx="11" cy="11" r="3" fill="#777"/><line x1="11" y1="0" x2="11" y2="4"/><line x1="11" y1="18" x2="11" y2="22"/><line x1="0" y1="11" x2="4" y2="11"/><line x1="18" y1="11" x2="22" y2="11"/></svg></span>
      </div>
      <div class="field">Pick an installation date
        <span class="field-btn"><svg width="20" height="20" viewBox="0 0 20 20" fill="none" stroke="#777" stroke-width="1.4"><rect x="1" y="3" width="18" height="16"/><line x1="1" y1="7" x2="19" y2="7"/><line x1="5" y1="1" x2="5" y2="5"/><line x1="15" y1="1" x2="15" y2="5"/><g fill="#777" stroke="none"><rect x="4" y="10" width="2" height="2"/><rect x="9" y="10" width="2" height="2"/><rect x="14" y="10" width="2" height="2"/><rect x="4" y="14" width="2" height="2"/><rect x="9" y="14" width="2" height="2"/><rect x="14" y="14" width="2" height="2"/></g></svg></span>
      </div>
      <div class="search-btn">
        <svg width="22" height="22" viewBox="0 0 22 22" fill="none" stroke="#fff" stroke-width="1.6"><circle cx="9" cy="9" r="7.5"/><line x1="14.5" y1="14.5" x2="21" y2="21"/></svg>
        Search
      </div>
    </form>
  </section>

  <footer class="site-footer">© 2017 Pebblebrook Plots.&nbsp; Terms of Use | Privacy Policy | Sitemap</footer>
</body>
</html>
```